K7 Services business card design contest. Use logo and create a professional layout.

See attached sample. Please sharpen all text and images, don't want any pix-elated content. We are looking for a clean look that quickly provides the information need. Please include our information provided on the sample card. Please feel free to offer any design changes. Please only user the colors provided: #2D3539 & #FFA500. Do not prefer any images other than the K7 Logo

Target Market(s)

Construction, Architects, General Contractors, residential

Industry/Entity Type

Business

Contact Information for Business Card

Company logo, Name, email, fax & phone

Font styles to use
Other font styles liked:
• Josefin Slab

Requirements
Must have
• Name
• Phone & Fax #'s
• address
• Logo
• Website url: www.kq7services.example
Nice to have
• Font Colors #2D3539 & #FFA400
• We prefer a white background.

```html
<!DOCTYPE html>
<html lang="en">
<head>
<meta charset="utf-8">
<title>K7 Services Business Card</title>
<link href="https://fonts.googleapis.com/css2?family=Montserrat:wght@300;400;600&display=swap" rel="stylesheet">
<style>
  :root {
    --ink: #2D3539;
    --accent: #F4A020;
    --paper: #FFFFFF;
    --backdrop: #D6D6D6;
  }
  * { margin: 0; padding: 0; box-sizing: border-box; }
  html, body {
    width: 1200px; height: 852px; overflow: hidden;
    background: var(--backdrop);
    font-family: "Montserrat", Arial, sans-serif;
    color: var(--ink);
  }
  .stage {
    position: relative; width: 1200px; height: 852px;
    display: flex; align-items: center; justify-content: center; gap: 40px;
  }
  .card {
    position: relative; width: 540px; height: 309px;
    background: var(--paper); border-radius: 12px; overflow: hidden;
  }
  /* Front */
  .front-brand {
    position: absolute; left: 0; right: 0; top: 50%; transform: translateY(-50%);
    display: flex; align-items: center; justify-content: center; gap: 18px;
  }
  .brand-dot {
    width: 58px; height: 58px; border: 7px solid var(--ink); border-radius: 50%; flex: none;
  }
  .brand-name { font-weight: 600; font-size: 44px; line-height: 1; letter-spacing: -0.5px; }
  .brand-tagline { font-weight: 600; font-size: 17px; margin-top: 4px; }
  /* Back */
  .big-mark {
    position: absolute; left: 52px; top: 70px; width: 160px; height: 160px;
    border: 16px solid var(--ink); border-radius: 50%;
  }
  .details { position: absolute; left: 262px; top: 30px; width: 260px; }
  .small-brand { display: flex; align-items: center; gap: 9px; }
  .small-brand .brand-dot { width: 28px; height: 28px; border-width: 4px; }
  .small-brand .brand-name { font-size: 21px; }
  .small-brand .brand-tagline { font-size: 9px; margin-top: 2px; }
  .person { margin-top: 12px; }
  .person-name { font-weight: 300; font-size: 16px; }
  .person-title { font-weight: 400; font-size: 10.5px; margin-top: 2px; }
  .contact { margin-top: 14px; list-style: none; font-size: 10.5px; font-weight: 400; }
  .contact li { display: flex; align-items: center; gap: 8px; line-height: 15px; }
  .contact svg { width: 10px; height: 10px; fill: var(--accent); flex: none; }
  .address { margin-top: 6px; font-size: 10.5px; line-height: 15px; }
  .service-band {
    position: absolute; left: 0; right: 0; bottom: 0; height: 82px;
    background: var(--accent);
  }
  .services {
    position: absolute; right: 22px; top: 10px;
    color: var(--paper); font-size: 14px; font-weight: 400; letter-spacing: 0.5px;
  }
</style>
</head>
<body>
<main class="stage">
  <section class="card card-front">
    <div class="front-brand">
      <span class="brand-dot"></span>
      <div>
        <div class="brand-name">K7 Services</div>
        <div class="brand-tagline">Clear Views From Above</div>
      </div>
    </div>
  </section>

  <section class="card card-back">
    <div class="service-band">
      <div class="services">DRONE | WEBCAM | VIDEO</div>
    </div>
    <div class="big-mark" aria-hidden="true"></div>
    <div class="details">
      <div class="small-brand">
        <span class="brand-dot"></span>
        <div>
          <div class="brand-name">K7 Services</div>
          <div class="brand-tagline">Clear Views From Above</div>
        </div>
      </div>
      <div class="person">
        <div class="person-name">Daniel R. Hollis, MBA</div>
        <div class="person-title">Director of Operations</div>
      </div>
      <ul class="contact">
        <li>
          <svg viewBox="0 0 10 10" aria-hidden="true"><path d="M2 0.5 L3.6 2.6 L2.7 3.6 Q3.8 5.8 6.3 7.3 L7.3 6.4 L9.5 8 L8.3 9.5 Q3.5 8.8 0.5 1.8 Z"/></svg>
          (555) 014 - 3827
        </li>
        <li>
          <svg viewBox="0 0 10 10" aria-hidden="true"><rect x="2.5" y="0.5" width="5" height="3"/><rect x="0.5" y="3.8" width="9" height="4"/><rect x="2.5" y="7" width="5" height="2.5"/></svg>
          (555) 014 - 6190
        </li>
        <li>
          <svg viewBox="0 0 10 10" aria-hidden="true"><circle cx="5" cy="5" r="4.5"/></svg>
          www.kq7services.example
        </li>
      </ul>
      <div class="address">1820 Alder Creek Lane, Suite<br>210-118 Marlow, Ohio, 45099</div>
    </div>
  </section>
</main>
</body>
</html>
```